Smile club flyer design

I am launching an office smile club and would like a design that sits my branding and that is appealing to customers. I have a design (I need a new one) that has all the information.
My website is maplehavendentalcarekx.com
Brand color is green. The design can be any color

Target Market(s)

Ages 30+

Industry/Entity Type

Dental

Font styles to use
Serif

Requirements
Must have
• Appealing to patients

```html
<!DOCTYPE html>
<html lang="en">
<head>
<meta charset="utf-8">
<title>Smile Club Membership Flyer – Maplehaven Dental Care</title>
<link rel="stylesheet" href="https://fonts.googleapis.com/css2?family=Bebas+Neue&family=Libre+Baskerville:wght@400;700&family=Mrs+Saint+Delafield&family=Poppins:ital,wght@0,600;0,700;1,600&family=Roboto+Condensed:wght@400;700&display=swap">
<style>
  :root{
    --page:#012812;
    --green:#0a8c3c;
    --green-dark:#0b6e33;
    --green-bright:#15a34a;
    --green-soft:#5fd190;
    --mint:#b3f7d2;
    --wash-top:#e4f5e6;
    --wash-bottom:#d2f0df;
    --card:#f0fdf4;
    --ink:#0b0b0b;
    --white:#ffffff;
  }
  *{box-sizing:border-box;margin:0;padding:0}
  html,body{width:924px;height:1200px;overflow:hidden;background:var(--page)}
  .flyer{position:absolute;left:174px;top:168px;width:576px;height:865px;overflow:hidden;background:linear-gradient(160deg,var(--wash-top),var(--wash-bottom));}
  .backdrop{position:absolute;inset:0}
  .abs{position:absolute}

  .brand{left:300px;top:22px;width:260px;text-align:center;color:var(--green)}
  .brand-name{font-family:"Libre Baskerville",serif;font-size:33px;line-height:1;letter-spacing:-.5px}
  .brand-sub{display:flex;align-items:center;justify-content:center;gap:6px;margin-top:6px;font-family:"Poppins",sans-serif;font-weight:600;font-size:13px;letter-spacing:4px;color:var(--green-dark)}
  .brand-sub::before,.brand-sub::after{content:"";width:26px;height:2px;background:var(--green-dark)}

  .headline{left:262px;top:100px;width:314px;text-align:center}
  .intro{font-family:"Mrs Saint Delafield",cursive;font-size:44px;line-height:1;color:var(--ink);position:relative;top:0;margin-left:-14px}
  .club{font-family:"Bebas Neue",sans-serif;font-size:70px;line-height:.8;color:var(--green);margin-top:-16px;letter-spacing:-.5px}
  .member{font-family:"Bebas Neue",sans-serif;font-size:79px;line-height:.82;color:var(--ink);margin-top:6px;letter-spacing:-1px}
  .tagline{font-family:"Roboto Condensed",sans-serif;font-weight:700;font-size:12.5px;color:var(--ink);margin-top:14px;letter-spacing:-.1px}

  .plan{position:absolute;top:393px;width:158px;height:210px;background:var(--card);box-shadow:0 2px 6px rgba(0,0,0,.25)}
  .plan-head{position:absolute;left:0;top:0;width:100%;height:100px}
  .plan-title{position:absolute;top:9px;width:100%;text-align:center;color:var(--white);font-family:"Libre Baskerville",serif;font-size:15px;line-height:1}
  .plan-sub{position:absolute;top:26px;width:100%;text-align:center;color:var(--mint);font-family:"Libre Baskerville",serif;font-size:11.5px;line-height:1}
  .price{position:absolute;left:54px;top:44px;width:50px;height:50px;border-radius:50%;background:var(--green);border:3px solid var(--white);color:var(--white);text-align:center;font-family:"Bebas Neue",sans-serif}
  .price b{display:block;font-weight:400;font-size:25px;line-height:1;margin-top:6px}
  .price small{display:block;font-size:9px;line-height:1}
  .perks{position:absolute;left:11px;top:109px;right:6px;list-style:none;font-family:"Roboto Condensed",sans-serif;font-size:9px;line-height:11px;color:var(--ink)}
  .perks li{position:relative;padding-left:15px;margin-bottom:6px}
  .perks li svg{position:absolute;left:0;top:1px;width:11px;height:8px}

  .finance{left:0;top:647px;width:335px;text-align:center;color:var(--white);font-family:"Poppins",sans-serif}
  .finance-title{font-size:11px;font-weight:700}
  .partners{display:flex;justify-content:center;gap:26px;margin-top:9px;font-size:19px;font-weight:700;line-height:1}
  .partners span{display:flex;align-items:center;gap:6px}
  .partners i{width:16px;height:16px;border-radius:50%;background:var(--white);display:block}
  .plans-note{font-size:10px;font-weight:600;letter-spacing:.8px;margin-top:11px}
  .fee{font-size:10.5px;font-style:italic;font-weight:600;margin-top:8px}
  .cta{font-family:"Bebas Neue",sans-serif;font-size:43px;line-height:1;margin-top:10px}
  .phone{font-family:"Bebas Neue",sans-serif;font-size:50px;line-height:1;margin-top:4px}

  .refresh{top:641px;left:354px;width:185px;height:193px}
  .refresh .plan-title{top:12px;font-size:18px}
  .refresh .plan-sub{top:32px;font-size:14px}
  .refresh .price{left:61px;top:50px;width:62px;height:62px}
  .refresh .price b{font-size:30px;margin-top:14px}
  .refresh .perks{top:131px;left:14px;font-size:10.5px;line-height:13px}
  .refresh .perks li{padding-left:18px;margin-bottom:7px}
  .refresh .perks li svg{top:2px;width:12px}
  .ribbon{position:absolute;left:0;top:0;width:46px;height:46px}
</style>
</head>
<body>
<main class="flyer">
  <svg class="backdrop" width="576" height="865" viewBox="0 0 576 865">
    <path d="M0,395 C130,440 240,390 370,325 C460,285 530,290 576,345 L576,865 L0,865 Z" fill="var(--green-soft)"/>
    <path d="M0,455 C140,470 260,410 390,350 C470,315 535,320 576,370 L576,865 L0,865 Z" fill="var(--green-bright)"/>
    <circle cx="140" cy="182" r="160" fill="none" stroke="var(--green)" stroke-width="14"/>
    <circle cx="140" cy="182" r="150" fill="none" stroke="var(--mint)" stroke-width="8"/>
    <g role="img" aria-label="Photo of a dental hygienist treating a smiling patient in the chair">
      <circle cx="140" cy="182" r="146" fill="#d6dadb"/>
    </g>
  </svg>

  <header class="abs brand">
    <div class="brand-name">Maplehaven</div>
    <div class="brand-sub">DENTAL CARE</div>
  </header>

  <section class="abs headline">
    <div class="intro">Introducing</div>
    <div class="club">SMILE CLUB</div>
    <div class="member">MEMBERSHIP</div>
    <div class="tagline">AFFORDABLE DENTAL CARE - NO INSURANCE REQUIRED</div>
  </section>

  <article class="plan" style="left:38px">
    <svg class="plan-head" viewBox="0 0 158 100" preserveAspectRatio="none"><path d="M0,0 H158 V32 Q79,105 0,32 Z" fill="var(--green)"/></svg>
    <div class="plan-title">CORE CARE</div>
    <div class="plan-sub">Preventive</div>
    <div class="price"><b>$39</b><small>/MONTH</small></div>
    <ul class="perks">
      <li><svg viewBox="0 0 11 8"><ellipse cx="2.5" cy="5" rx="2.5" ry="1.4" transform="rotate(30 2.5 5)" fill="var(--green)"/><ellipse cx="8.5" cy="5" rx="2.5" ry="1.4" transform="rotate(-30 8.5 5)" fill="var(--green)"/><ellipse cx="5.5" cy="3" rx="1.3" ry="2.8" fill="var(--green)"/></svg>Comprehensive Annual Exam</li>
      <li><svg viewBox="0 0 11 8"><ellipse cx="2.5" cy="5" rx="2.5" ry="1.4" transform="rotate(30 2.5 5)" fill="var(--green)"/><ellipse cx="8.5" cy="5" rx="2.5" ry="1.4" transform="rotate(-30 8.5 5)" fill="var(--green)"/><ellipse cx="5.5" cy="3" rx="1.3" ry="2.8" fill="var(--green)"/></svg>2 Professional Cleanings per Year</li>
      <li><svg viewBox="0 0 11 8"><ellipse cx="2.5" cy="5" rx="2.5" ry="1.4" transform="rotate(30 2.5 5)" fill="var(--green)"/><ellipse cx="8.5" cy="5" rx="2.5" ry="1.4" transform="rotate(-30 8.5 5)" fill="var(--green)"/><ellipse cx="5.5" cy="3" rx="1.3" ry="2.8" fill="var(--green)"/></svg>Routine Bitewing X-rays</li>
      <li><svg viewBox="0 0 11 8"><ellipse cx="2.5" cy="5" rx="2.5" ry="1.4" transform="rotate(30 2.5 5)" fill="var(--green)"/><ellipse cx="8.5" cy="5" rx="2.5" ry="1.4" transform="rotate(-30 8.5 5)" fill="var(--green)"/><ellipse cx="5.5" cy="3" rx="1.3" ry="2.8" fill="var(--green)"/></svg>10% Savings on Treatment</li>
    </ul>
  </article>

  <article class="plan" style="left:209px">
    <svg class="plan-head" viewBox="0 0 158 100" preserveAspectRatio="none"><path d="M0,0 H158 V32 Q79,105 0,32 Z" fill="var(--green-dark)"/></svg>
    <div class="plan-title">BRIGHT</div>
    <div class="plan-sub">Cosmetic</div>
    <div class="price" style="background:var(--green-dark)"><b>$59</b><small>/MONTH</small></div>
    <ul class="perks">
      <li><svg viewBox="0 0 11 8"><ellipse cx="2.5" cy="5" rx="2.5" ry="1.4" transform="rotate(30 2.5 5)" fill="var(--green)"/><ellipse cx="8.5" cy="5" rx="2.5" ry="1.4" transform="rotate(-30 8.5 5)" fill="var(--green)"/><ellipse cx="5.5" cy="3" rx="1.3" ry="2.8" fill="var(--green)"/></svg>Annual In-Office Whitening<br>(Top &amp; Bottom)</li>
      <li><svg viewBox="0 0 11 8"><ellipse cx="2.5" cy="5" rx="2.5" ry="1.4" transform="rotate(30 2.5 5)" fill="var(--green)"/><ellipse cx="8.5" cy="5" rx="2.5" ry="1.4" transform="rotate(-30 8.5 5)" fill="var(--green)"/><ellipse cx="5.5" cy="3" rx="1.3" ry="2.8" fill="var(--green)"/></svg>Custom Whitening Trays</li>
      <li><svg viewBox="0 0 11 8"><ellipse cx="2.5" cy="5" rx="2.5" ry="1.4" transform="rotate(30 2.5 5)" fill="var(--green)"/><ellipse cx="8.5" cy="5" rx="2.5" ry="1.4" transform="rotate(-30 8.5 5)" fill="var(--green)"/><ellipse cx="5.5" cy="3" rx="1.3" ry="2.8" fill="var(--green)"/></svg>15% Savings on Elective Treatment</li>
    </ul>
  </article>

  <article class="plan" style="left:380px">
    <svg class="plan-head" viewBox="0 0 158 100" preserveAspectRatio="none"><path d="M0,0 H158 V32 Q79,105 0,32 Z" fill="var(--green)"/></svg>
    <div class="plan-title">TOTAL SMILE</div>
    <div class="plan-sub">Periodontal</div>
    <div class="price"><b>$89</b><small>/MONTH</small></div>
    <ul class="perks">
      <li><svg viewBox="0 0 11 8"><ellipse cx="2.5" cy="5" rx="2.5" ry="1.4" transform="rotate(30 2.5 5)" fill="var(--green)"/><ellipse cx="8.5" cy="5" rx="2.5" ry="1.4" transform="rotate(-30 8.5 5)" fill="var(--green)"/><ellipse cx="5.5" cy="3" rx="1.3" ry="2.8" fill="var(--green)"/></svg>3-4 Perio Maintenance Visits<br>per Year</li>
      <li><svg viewBox="0 0 11 8"><ellipse cx="2.5" cy="5" rx="2.5" ry="1.4" transform="rotate(30 2.5 5)" fill="var(--green)"/><ellipse cx="8.5" cy="5" rx="2.5" ry="1.4" transform="rotate(-30 8.5 5)" fill="var(--green)"/><ellipse cx="5.5" cy="3" rx="1.3" ry="2.8" fill="var(--green)"/></svg>1 Comprehensive Exam</li>
      <li><svg viewBox="0 0 11 8"><ellipse cx="2.5" cy="5" rx="2.5" ry="1.4" transform="rotate(30 2.5 5)" fill="var(--green)"/><ellipse cx="8.5" cy="5" rx="2.5" ry="1.4" transform="rotate(-30 8.5 5)" fill="var(--green)"/><ellipse cx="5.5" cy="3" rx="1.3" ry="2.8" fill="var(--green)"/></svg>Diagnostic X-rays</li>
      <li><svg viewBox="0 0 11 8"><ellipse cx="2.5" cy="5" rx="2.5" ry="1.4" transform="rotate(30 2.5 5)" fill="var(--green)"/><ellipse cx="8.5" cy="5" rx="2.5" ry="1.4" transform="rotate(-30 8.5 5)" fill="var(--green)"/><ellipse cx="5.5" cy="3" rx="1.3" ry="2.8" fill="var(--green)"/></svg>15% Savings on Restorative &amp;<br>Elective Care</li>
    </ul>
  </article>

  <section class="abs finance">
    <div class="finance-title">FLEXIBLE FINANCING FOR TREATMENTS</div>
    <div class="partners"><span><i></i>FlexPay</span><span><i></i>Bloomly</span></div>
    <div class="plans-note">PAYMENT PLANS AVAILABLE</div>
    <div class="fee">*$49 Lifetime Activation Fee (Non-refundable)</div>
    <div class="cta">JOIN SMILE CLUB TODAY!</div>
    <div class="phone">865-555-0142</div>
  </section>

  <article class="plan refresh">
    <svg class="plan-head" style="height:120px" viewBox="0 0 185 120" preserveAspectRatio="none"><path d="M0,0 H185 V38 Q92,118 0,38 Z" fill="var(--green-dark)"/></svg>
    <svg class="ribbon" viewBox="0 0 46 46"><path d="M0,46 L46,0 L30,0 L0,30 Z" fill="var(--green)"/><text x="14" y="24" transform="rotate(-45 14 24)" fill="var(--white)" font-family="Libre Baskerville, serif" font-size="9">NEW</text></svg>
    <div class="plan-title">SMILE</div>
    <div class="plan-sub">Refresh Package</div>
    <div class="price" style="background:var(--green-dark)"><b>$499</b></div>
    <ul class="perks">
      <li><svg viewBox="0 0 11 8"><ellipse cx="2.5" cy="5" rx="2.5" ry="1.4" transform="rotate(30 2.5 5)" fill="var(--green)"/><ellipse cx="8.5" cy="5" rx="2.5" ry="1.4" transform="rotate(-30 8.5 5)" fill="var(--green)"/><ellipse cx="5.5" cy="3" rx="1.3" ry="2.8" fill="var(--green)"/></svg>Cleaning + Comprehensive Exam +<br>Whitening</li>
      <li><svg viewBox="0 0 11 8"><ellipse cx="2.5" cy="5" rx="2.5" ry="1.4" transform="rotate(30 2.5 5)" fill="var(--green)"/><ellipse cx="8.5" cy="5" rx="2.5" ry="1.4" transform="rotate(-30 8.5 5)" fill="var(--green)"/><ellipse cx="5.5" cy="3" rx="1.3" ry="2.8" fill="var(--green)"/></svg>Limited Time Offer</li>
    </ul>
  </article>
</main>
</body>
</html>
```